Design 4 pages for an event discovery website

This is a contest for the design of 4 pages for an events discovery website. The feature is part of the new sign-up process.

Please see the attached document for a full scope, mockups and the parent category icons.

Target Market(s)

18-35 Australian event goers

Industry/Entity Type

Events

Number of Pages Required

4 page

```html
<!DOCTYPE html>
<html lang="en">
<head>
<meta charset="utf-8">
<title>eventora – Sign Up</title>
<link rel="stylesheet" href="https://fonts.googleapis.com/css2?family=Open+Sans:ital,wght@0,400;0,600;0,700;1,600;1,700&display=swap">
<style>
  :root {
    --ink: #000000;
    --white: #ffffff;
    --rule: #5a5a5a;
    --field-text: #3a3a3a;
    --field-border: #c9c9c9;
    --placeholder-grey: #8a8a8a;
    --blue-top: #3fb8f2;
    --blue-bottom: #1a93dc;
    --bullet: #27a6ea;
    --panel-frame: rgba(90, 90, 90, 0.55);
    --panel: #000000;
    --bokeh-deep: #1a0309;
    --bokeh-red: #8e0f2e;
    --bokeh-magenta: #6d1450;
  }
  * { box-sizing: border-box; margin: 0; padding: 0; }
  html, body { width: 1200px; height: 792px; overflow: hidden; background: var(--ink); }
  body { font-family: "Open Sans", Arial, sans-serif; color: var(--white); position: relative; }

  .site-header {
    position: absolute; left: 0; top: 0; width: 1200px; height: 98px;
    background: var(--ink); border-bottom: 1px solid var(--rule);
  }
  .brand {
    position: absolute; left: 36px; top: 24px; display: flex; align-items: center; gap: 10px;
    font-weight: 700; font-size: 46px; line-height: 1; color: var(--white); letter-spacing: -1px;
  }
  .brand-dot { width: 26px; height: 26px; border-radius: 50%; background: var(--bullet); }
  .nav-find {
    position: absolute; left: 302px; top: 37px; font-size: 12px; font-weight: 600; color: var(--white);
  }
  .search {
    position: absolute; left: 786px; top: 30px; width: 204px; height: 38px;
    background: var(--white); border-radius: 3px; display: flex; align-items: center;
    padding: 0 12px; font-size: 15px; color: var(--placeholder-grey);
  }
  .search svg { position: absolute; right: 12px; top: 10px; }
  .account-links {
    position: absolute; left: 1019px; top: 39px; font-size: 15px; font-weight: 600; color: var(--white);
  }
  .account-links .divider { margin: 0 8px; }

  .stage {
    position: absolute; left: 0; top: 99px; width: 1200px; height: 633px;
    background:
      radial-gradient(circle at 20% 30%, rgba(200, 20, 60, 0.55) 0, transparent 14%),
      radial-gradient(circle at 42% 90%, rgba(180, 15, 50, 0.6) 0, transparent 18%),
      radial-gradient(circle at 88% 80%, rgba(170, 20, 70, 0.55) 0, transparent 16%),
      radial-gradient(circle at 70% 95%, rgba(130, 25, 90, 0.5) 0, transparent 18%),
      radial-gradient(circle at 95% 20%, rgba(150, 20, 60, 0.45) 0, transparent 14%),
      linear-gradient(180deg, var(--bokeh-deep) 0%, var(--bokeh-red) 70%, var(--bokeh-magenta) 100%);
  }

  .signup-form { position: absolute; left: 56px; top: 152px; width: 344px; }
  .signup-title { font-size: 31px; font-weight: 600; line-height: 1; margin-bottom: 27px; }
  .field {
    display: block; width: 344px; height: 48px; margin-bottom: 13px;
    background: var(--white); border: 1px solid var(--field-border); border-radius: 3px;
    padding: 0 15px; line-height: 46px; font-size: 17px; color: var(--field-text);
  }
  .submit {
    display: block; width: 344px; height: 48px; margin-top: 18px; border-radius: 3px;
    background: linear-gradient(180deg, var(--blue-top), var(--blue-bottom));
    text-align: center; line-height: 48px; font-size: 17px; font-weight: 600; color: var(--white);
  }

  .benefits-frame {
    position: absolute; left: 451px; top: 162px; width: 709px; height: 394px;
    background: var(--panel-frame); border-radius: 3px;
  }
  .benefits {
    position: absolute; left: 12px; top: 11px; width: 685px; height: 371px;
    background: var(--panel); border-radius: 3px; list-style: none; padding-top: 25px;
  }
  .benefit {
    display: flex; align-items: center; height: 58px; padding-left: 28px;
    font-size: 17.5px; font-weight: 700; font-style: italic;
  }
  .benefit svg { flex: none; margin-right: 16px; }

  .site-footer {
    position: absolute; left: 0; top: 732px; width: 1200px; height: 60px;
    background: var(--ink); border-top: 1px solid var(--rule);
    text-align: center; line-height: 58px; font-size: 15px; font-weight: 600;
  }
</style>
</head>
<body>
  <header class="site-header">
    <div class="brand"><span class="brand-dot"></span>eventora</div>
    <div class="nav-find">FIND EVENT</div>
    <div class="search">search
      <svg width="18" height="18" viewBox="0 0 18 18"><circle cx="7" cy="7" r="5.5" fill="none" stroke="#b5b5b5" stroke-width="2"/><line x1="11" y1="11" x2="16" y2="16" stroke="#b5b5b5" stroke-width="2.5" stroke-linecap="round"/></svg>
    </div>
    <nav class="account-links">SIGN UP<span class="divider">|</span>LOGIN</nav>
  </header>

  <main class="stage" role="img" aria-label="Blurred party lights background in deep red and magenta tones">
  </main>

  <form class="signup-form">
    <h1 class="signup-title">Sign Up</h1>
    <span class="field">User Name</span>
    <span class="field">Email Address</span>
    <span class="field">Password</span>
    <span class="field">Confirm Password</span>
    <span class="field">First Name</span>
    <span class="field">Last Name</span>
    <span class="field">Date of Birth</span>
    <span class="submit">SIGN UP NOW</span>
  </form>

  <section class="benefits-frame">
    <ul class="benefits">
      <li class="benefit"><svg width="22" height="22" viewBox="0 0 22 22"><circle cx="11" cy="11" r="11" fill="var(--bullet)"/><path d="M9.5 7.5 L13 11 L9.5 14.5" fill="none" stroke="#fff" stroke-width="1.8"/></svg>Get personalised event recommendations</li>
      <li class="benefit"><svg width="22" height="22" viewBox="0 0 22 22"><circle cx="11" cy="11" r="11" fill="var(--bullet)"/><path d="M9.5 7.5 L13 11 L9.5 14.5" fill="none" stroke="#fff" stroke-width="1.8"/></svg>Get notified about your favourite events - never miss out again</li>
      <li class="benefit"><svg width="22" height="22" viewBox="0 0 22 22"><circle cx="11" cy="11" r="11" fill="var(--bullet)"/><path d="M9.5 7.5 L13 11 L9.5 14.5" fill="none" stroke="#fff" stroke-width="1.8"/></svg>Follow all your favourite artists, musicians, teams and players in one place</li>
      <li class="benefit"><svg width="22" height="22" viewBox="0 0 22 22"><circle cx="11" cy="11" r="11" fill="var(--bullet)"/><path d="M9.5 7.5 L13 11 L9.5 14.5" fill="none" stroke="#fff" stroke-width="1.8"/></svg>Follow your favourite local venues to know everything happening there</li>
      <li class="benefit"><svg width="22" height="22" viewBox="0 0 22 22"><circle cx="11" cy="11" r="11" fill="var(--bullet)"/><path d="M9.5 7.5 L13 11 L9.5 14.5" fill="none" stroke="#fff" stroke-width="1.8"/></svg>Get curated news and feature content on your favourite artists (coming soon)</li>
      <li class="benefit"><svg width="22" height="22" viewBox="0 0 22 22"><circle cx="11" cy="11" r="11" fill="var(--bullet)"/><path d="M9.5 7.5 L13 11 L9.5 14.5" fill="none" stroke="#fff" stroke-width="1.8"/></svg>Invite your mates to events via Matesnet (MN sign-up only</li>
    </ul>
  </section>

  <footer class="site-footer">© 2015 eventora. All Rights Reserved.</footer>
</body>
</html>
```